Quillmere Supply Chain and Logistic Consulting

Please review the attached Business Card. I want as close to this card with the colors, fonts, and quality of the card as possible. The attached compass should replace the deer head on both sides of the card and the text should say:

Backside
Compass JPEG
Quillmere SC&L
A Supply Chain and Logistics Consulting Company

Frontside
Quillmere SC&L
Ray Falkner - Dorvale Ohio
President
____________________________________
(555) 314-9027
QuillmereSCL@Examplemail.com
_____________________________________

Bottom Front Side

Target Market(s)

Businesses

Contact Information for Business Card

Backside
Compass JPEG
Quillmere SC&L

Frontside
Quillmere SC&L
President
(555) 314-9027
QuillmereSCL@Examplemail.com

Bottom Front Side

Font styles to use
Serif
Script

Colors

Designer to choose colors to be used in the design.

Requirements
Must have
• See attached card for reference
Nice to have
Should not have

```html
<!DOCTYPE html>
<html lang="en">
<head>
<meta charset="utf-8">
<title>Quillmere SC&amp;L Business Card</title>
<link rel="stylesheet" href="https://fonts.googleapis.com/css2?family=Cinzel:wght@400;500&family=Tinos:wght@400;700&display=swap">
<style>
  :root {
    --backdrop: #3a3a3d;
    --card: #1f2023;
    --card-edge: #2a2b2f;
    --text-bright: #f2f2f2;
    --text-muted: #a9a9ad;
    --text-soft: #c9c9cc;
    --compass-blue: #3b5478;
    --rule: #6b6b70;
  }
  * { margin: 0; padding: 0; box-sizing: border-box; }
  html, body { width: 1200px; height: 1108px; overflow: hidden; }
  body {
    background: var(--backdrop);
    display: flex;
    justify-content: center;
    align-items: center;
    gap: 64px;
  }
  .card {
    width: 500px;
    height: 820px;
    background: var(--card);
    border: 1px solid var(--card-edge);
    border-radius: 28px;
    box-shadow: 0 18px 40px rgba(0,0,0,.45);
    position: relative;
    overflow: hidden;
    text-align: center;
  }
  .front { padding-top: 70px; }
  .brand-mark {
    width: 250px; height: 250px;
    margin: 0 auto;
    border-radius: 50%;
    background: var(--compass-blue);
  }
  .brand-name {
    margin-top: 34px;
    font-family: "Cinzel", serif;
    font-weight: 400;
    font-size: 40px;
    color: var(--text-bright);
    letter-spacing: 1px;
  }
  .person-name {
    margin-top: 38px;
    font-family: "Tinos", serif;
    font-weight: 700;
    font-size: 28px;
    color: var(--text-muted);
  }
  .person-title {
    font-family: "Tinos", serif;
    font-size: 23px;
    color: var(--text-muted);
    margin-top: 2px;
  }
  .rule {
    width: 340px; height: 1px;
    margin: 16px auto;
    background: linear-gradient(90deg, transparent, var(--rule), transparent);
  }
  .contact {
    font-family: "Tinos", serif;
    font-size: 24px;
    line-height: 1.3;
    color: var(--text-soft);
  }
  .tagline {
    font-family: "Cinzel", serif;
    font-size: 23px;
    line-height: 1.25;
    color: var(--text-muted);
    letter-spacing: .5px;
  }
  .back-pattern {
    position: absolute;
    top: 0; left: 0; right: 0;
    height: 560px;
    background: linear-gradient(180deg, #2b2c30 0%, #25262a 60%, var(--card) 100%);
  }
  .back-mark {
    position: absolute;
    top: 565px; left: 50%;
    width: 80px; height: 80px;
    margin-left: -40px;
    border-radius: 50%;
    background: var(--compass-blue);
  }
  .back .tagline {
    position: absolute;
    top: 690px; left: 0; right: 0;
  }
</style>
</head>
<body>
  <section class="card front">
    <div class="brand-mark" aria-hidden="true"></div>
    <h1 class="brand-name">QUILLMERE SC&amp;L</h1>
    <p class="person-name">Ray Falkner - Dorvale Ohio</p>
    <p class="person-title">President</p>
    <div class="rule"></div>
    <p class="contact">(555) 314-9027<br>QuillmereSCL@Examplemail.com</p>
    <div class="rule"></div>
    <p class="tagline">A Supply Chain and Logistics<br>Consulting Company</p>
  </section>

  <section class="card back">
    <div class="back-pattern" role="img" aria-label="Faint repeating compass rose pattern"></div>
    <div class="back-mark" aria-hidden="true"></div>
    <p class="tagline">A Supply Chain and Logistics<br>Consulting Company</p>
  </section>
</body>
</html>
```